Brovo like IOS/Android app for Okinawa Island - TaruSeeker

TaruSeeker is the name of the app
The closest thing that I can relate this app to is a region specific Brovo app. The app is for the island of Okinawa and is geared towards English speaking travelers. The style of app that I prefer is a look and feel similar to that of the new Nestory app, color should also be similar if not the same as the nestory app.

The app needs to have the following screens

LOGIN SCREEN
1. App login page with a login for chatterly button or create an account option. Personally I would like an image in the background with a real beachy feel, but don't do this if it messes with your design.

2. Depending on the choice of login there will need to be a second login screen to create the account. Nestory does this nicely.

PRIMARY HOME
primary page similar to the primary layout when you get into the nestory app.
This page is kind of like the home page of the app and should include the following items:
search field
upcoming events
popular things to do
featured restaurants
Featured Places to stay
area guides
Moving here
(this will allow the person to select, housing agencies, auto dealers, schools etc) These are essentially just quick searches.
Each selection should be listed so that the user can swipe to the left or right in order to view more listings under the categories listed above. It will not be the full list but rather a sample.

SIDEBAR POPOUT MENU
Popout sidebar that contains the following selections
Places to Eat
Things to do
Attractions
Beaches
Shop
Farmers Markets
Places to Stay
Schools & DayCare
Housing
Auto
Events
Account settings
Add a business

LIST VIEW
4. List view page for whatever category the user selected. This will show all the listings for the specific category: The top should also have the featured listings for that category

INDIVIDUAL LISTING
5. Listing page
This will include photos, description, hours, map(this can be a button to view the map or the map), Reviews with a leave a review option

AREA GUIDES
6. Area Guides. This is where the user will be able to select a specific area and learn about it. It should include an area where there can be a description, photos with a hero photo image, a map, popular local attractions or things to do, best restaurants in the area, places to stay etc.

PROFILE PAGE
7. Profile page for the user where they can make any updates they need to

Every page but the listing page should include the search bar. When the user clicks in it they should be able to see a drop down of quick select searches or run a regular search.

Logo
I have attached a logo that was made that needs a redesign. The map marker contains the logo for Okinawa within it so it does need to be similar.

If you have any questions or need clarification please send me a message. I will respond promptly.
Thank you,

Industry/Entity Type

Android

Logo Text

TaruSeeker

```html
<!DOCTYPE html>
<html lang="en">
<head>
<meta charset="utf-8">
<title>TaruSeeker – Attractions</title>
<link href="https://fonts.googleapis.com/css2?family=Montserrat:wght@500;700&family=Inter:wght@400;500&family=Noto+Sans+JP:wght@400&display=swap" rel="stylesheet">
<style>
  :root{
    --page-bg:#efefef;
    --screen-bg:#ffffff;
    --ink:#262626;
    --muted:#666666;
    --accent:#e8536a;
    --divider:#e6e6e6;
  }
  *{box-sizing:border-box;margin:0;padding:0}
  html,body{width:1200px;height:1200px;overflow:hidden}
  body{background:var(--page-bg);position:relative;font-family:"Montserrat",sans-serif;color:var(--ink)}
  .screen{position:absolute;left:300px;top:66px;width:600px;height:1068px;background:var(--screen-bg);overflow:hidden;box-shadow:0 10px 60px rgba(0,0,0,.12)}
  .top-bar{height:102px;background:linear-gradient(#f7f7f7,#fdfdfd);border-bottom:1px solid var(--accent);position:relative}
  .status-bar{height:44px;display:flex;align-items:center;justify-content:space-between;padding:0 12px;font-family:"Inter",sans-serif;font-size:18px;font-weight:500;color:#111}
  .status-left,.status-right{display:flex;align-items:center;gap:6px;width:200px}
  .status-right{justify-content:flex-end}
  .nav{position:absolute;left:0;right:0;top:44px;height:50px;display:flex;align-items:center;justify-content:center}
  .nav-back{position:absolute;left:27px;top:12px}
  .nav-title{font-size:22px;font-weight:700;color:var(--ink)}
  .listing{list-style:none;padding:0 29px}
  .listing-item{display:flex;gap:23px;height:200px;padding-top:32px;border-bottom:1px solid var(--divider)}
  .listing-photo{width:168px;height:168px;flex:none}
  .listing-body{display:flex;flex-direction:column}
  .listing-kana{font-family:"Noto Sans JP",sans-serif;font-size:17px;color:var(--muted);line-height:24px}
  .listing-name{font-size:28px;font-weight:700;line-height:38px;margin-top:8px;letter-spacing:-.2px}
  .listing-place{display:flex;align-items:center;gap:8px;margin-top:16px;color:var(--accent);font-size:23px;font-weight:500}
  .photo-sunset{background:linear-gradient(180deg,#6b6a72 0%,#a79a8c 40%,#e8a640 58%,#4a4038 80%,#2a2a2e 100%)}
  .photo-aquarium{background:linear-gradient(180deg,#1a8fd0 0%,#18a4e0 55%,#0b5e98 82%,#04121f 100%)}
  .photo-farm{background:linear-gradient(180deg,#3f7a32 0%,#5c8c40 35%,#7a5c48 60%,#b5a08a 85%,#cfc2b0 100%)}
  .photo-stars{background:radial-gradient(ellipse at 55% 45%,#5a6448 0%,#2a3024 45%,#0c0f0b 100%)}
  .photo-port{background:linear-gradient(180deg,#4a3c1c 0%,#2a2412 40%,#c8a040 75%,#3a3020 100%)}
</style>
</head>
<body>
<main class="screen">
  <header class="top-bar">
    <div class="status-bar">
      <div class="status-left">
        <svg width="56" height="12" viewBox="0 0 56 12"><g fill="#111"><circle cx="6" cy="6" r="5"/><circle cx="18" cy="6" r="5"/><circle cx="30" cy="6" r="5"/></g><g fill="none" stroke="#111" stroke-width="1"><circle cx="42" cy="6" r="4.5"/><circle cx="53" cy="6" r="2.5"/></g></svg>
        <span>Carrier</span>
        <svg width="20" height="16" viewBox="0 0 20 16"><path d="M10 15 L2 6 A11 11 0 0 1 18 6 Z" fill="#111"/></svg>
      </div>
      <span>4:21 PM</span>
      <div class="status-right">
        <svg width="12" height="20" viewBox="0 0 12 20"><path d="M2 5 L10 14 L6 18 V2 L10 6 L2 15" fill="none" stroke="#777" stroke-width="1.4"/></svg>
        <span>100%</span>
        <svg width="40" height="18" viewBox="0 0 40 18"><rect x="1" y="2" width="34" height="14" rx="2" fill="none" stroke="#111" stroke-width="1.5"/><rect x="3" y="4" width="30" height="10" fill="#111"/><rect x="36" y="6" width="2.5" height="6" fill="#111"/></svg>
      </div>
    </div>
    <nav class="nav">
      <svg class="nav-back" width="30" height="24" viewBox="0 0 30 24"><path d="M29 12 H2 M12 2 L2 12 L12 22" fill="none" stroke="var(--accent)" stroke-width="2"/></svg>
      <h1 class="nav-title">Attractions</h1>
    </nav>
  </header>

  <ul class="listing">
    <li class="listing-item">
      <div class="listing-photo photo-sunset" role="img" aria-label="Paddleboarder on calm water at sunset"></div>
      <div class="listing-body">
        <span class="listing-kana">ナミサップ</span>
        <h2 class="listing-name">Nami-SUP takes you places</h2>
        <span class="listing-place"><svg width="22" height="28" viewBox="0 0 22 28"><path d="M11 26 C4 17 2 13 2 10 A9 9 0 0 1 20 10 C20 13 18 17 11 26 Z" fill="none" stroke="var(--accent)" stroke-width="1.8"/><circle cx="11" cy="10" r="3.5" fill="none" stroke="var(--accent)" stroke-width="1.8"/></svg>Minato Town</span>
      </div>
    </li>
    <li class="listing-item">
      <div class="listing-photo photo-aquarium" role="img" aria-label="Visitors before a large aquarium tank with a whale shark"></div>
      <div class="listing-body">
        <span class="listing-kana">珊瑚湾公園</span>
        <h2 class="listing-name">Coral Bay Park</h2>
        <span class="listing-place"><svg width="22" height="28" viewBox="0 0 22 28"><path d="M11 26 C4 17 2 13 2 10 A9 9 0 0 1 20 10 C20 13 18 17 11 26 Z" fill="none" stroke="var(--accent)" stroke-width="1.8"/><circle cx="11" cy="10" r="3.5" fill="none" stroke="var(--accent)" stroke-width="1.8"/></svg>Sango Town</span>
      </div>
    </li>
    <li class="listing-item">
      <div class="listing-photo photo-farm" role="img" aria-label="Cattle behind a wooden fence on a green farm"></div>
      <div class="listing-body">
        <span class="listing-kana">かぜファーム</span>
        <h2 class="listing-name">Kaze Farm</h2>
        <span class="listing-place"><svg width="22" height="28" viewBox="0 0 22 28"><path d="M11 26 C4 17 2 13 2 10 A9 9 0 0 1 20 10 C20 13 18 17 11 26 Z" fill="none" stroke="var(--accent)" stroke-width="1.8"/><circle cx="11" cy="10" r="3.5" fill="none" stroke="var(--accent)" stroke-width="1.8"/></svg>Hoshino City</span>
      </div>
    </li>
    <li class="listing-item">
      <div class="listing-photo photo-stars" role="img" aria-label="Planetarium dome showing the Milky Way"></div>
      <div class="listing-body">
        <span class="listing-kana">潮風文化館</span>
        <h2 class="listing-name">Seafaring Heritage Museum</h2>
        <span class="listing-place"><svg width="22" height="28" viewBox="0 0 22 28"><path d="M11 26 C4 17 2 13 2 10 A9 9 0 0 1 20 10 C20 13 18 17 11 26 Z" fill="none" stroke="var(--accent)" stroke-width="1.8"/><circle cx="11" cy="10" r="3.5" fill="none" stroke="var(--accent)" stroke-width="1.8"/></svg>Sango-cho</span>
      </div>
    </li>
    <li class="listing-item">
      <div class="listing-photo photo-port" role="img" aria-label="Lit ferry docked at the harbour at night"></div>
      <div class="listing-body">
        <span class="listing-kana">海風港</span>
        <h2 class="listing-name">Umikaze Port</h2>
        <span class="listing-place"><svg width="22" height="28" viewBox="0 0 22 28"><path d="M11 26 C4 17 2 13 2 10 A9 9 0 0 1 20 10 C20 13 18 17 11 26 Z" fill="none" stroke="var(--accent)" stroke-width="1.8"/><circle cx="11" cy="10" r="3.5" fill="none" stroke="var(--accent)" stroke-width="1.8"/></svg>Umikaze City</span>
      </div>
    </li>
  </ul>
</main>
</body>
</html>
```